TLMWOS - Website Design

We require a WordPress website for an accounting firm.
Please review our concept design found on our development site:
http://quillmarsh.ca/tlmwoxe.
The client would like to carry the look and feel of the National Corporate site http://www.tlm.ca as well.
The site must be mobile ready (responsive)
The client will be providing a collection of staff photos for a contact page
Accounting

```html
<!DOCTYPE html>
<html lang="en">
<head>
<meta charset="utf-8">
<title>TLM Woxley Osler &amp; Associates</title>
<link href="https://fonts.googleapis.com/css2?family=Open+Sans:wght@400;600;700&family=Cinzel:wght@500&display=swap" rel="stylesheet">
<style>
:root{
  --olive:#7d7a34;
  --olive-box:rgba(128,126,52,.86);
  --olive-dark:#6f6c2c;
  --ink:#3a3a3a;
  --muted:#8a8a8a;
  --panel:#f4f4f4;
  --rule:#dedede;
  --date:#4a4a4a;
  --footer:#2b2b2b;
  --footer-text:#b4b4b4;
}
*{box-sizing:border-box;margin:0;padding:0}
html,body{width:1021px;height:1200px;overflow:hidden}
body{position:relative;font-family:"Open Sans",Arial,sans-serif;color:var(--ink);background:#fff}
.scenery{position:absolute;left:0;top:0;width:1021px;height:1106px;
  background:
   linear-gradient(180deg,#c3b7ad 0%,#d9c9bb 16%,#b9aab1 24%,#8e8aa3 30%,#a8a6b8 37%,#c9c3c4 40%,#9aa46a 44%,#7f9a3c 55%,#6b8a2e 70%,#88a33a 85%,#9aad3e 100%);}
.scenery::after{content:"";position:absolute;inset:0;background:linear-gradient(90deg,rgba(200,160,60,.25),transparent 30%,transparent 70%,rgba(40,70,40,.3))}
.header{position:absolute;left:83px;top:0;width:853px;height:78px;background:#fff}
.brand{position:absolute;left:12px;top:14px;display:flex;align-items:center;gap:10px}
.brand-mark{width:44px;height:44px;border:2px solid var(--olive)}
.brand-name{font-family:"Cinzel",serif;font-weight:500;font-size:18px;color:#2c2c2c;line-height:1}
.brand-tag{font-family:"Cinzel",serif;font-size:11.5px;color:#2c2c2c;margin-top:6px;padding-bottom:3px;border-bottom:2px solid var(--olive)}
.search{position:absolute;left:667px;top:16px;width:173px;height:19px;border-bottom:1px solid var(--rule);font-size:8.5px;color:var(--muted);padding-top:3px}
.search svg{position:absolute;right:2px;top:4px}
.nav{position:absolute;right:13px;top:51px;display:flex;gap:29px;font-size:10.5px;color:#555;list-style:none}
.nav .active{color:var(--olive)}
.hero-title{position:absolute;left:86px;top:140px;font-size:29px;color:#fff;font-weight:600;text-shadow:0 1px 3px rgba(0,0,0,.35)}
.slide-arrow{position:absolute;top:303px;width:22px;height:30px;background:rgba(40,40,40,.55)}
.slide-arrow.left{left:0}.slide-arrow.right{right:0}
.slide-arrow svg{position:absolute;left:6px;top:8px}
.features{position:absolute;left:83px;top:408px;width:853px;height:150px;display:flex;gap:2px}
.feature{flex:1;background:var(--olive-box);color:#fff;padding:14px 15px}
.feature h2{font-size:24px;font-weight:600;margin-top:8px;line-height:1.2}
.feature h2 small{font-size:16px;font-weight:600}
.feature p{font-size:8.3px;line-height:1.6;margin-top:6px;color:#f0efdc}
.main{position:absolute;left:83px;top:558px;width:612px;height:548px;background:#fff;padding:28px 25px 0}
.main h1{font-size:21px;font-weight:600;color:var(--olive)}
.lead{font-size:11.6px;font-weight:600;line-height:1.52;color:#444;margin-top:12px}
.copy{font-size:9.2px;line-height:1.75;color:var(--muted);margin-top:12px}
.intro-row{display:flex;gap:18px;margin-top:10px}
.desk-photo{flex:0 0 160px;height:144px;background:linear-gradient(135deg,#6e4a2c,#a8835b 45%,#3d4a5a 70%,#2c2c33)}
.intro-row .copy{margin-top:0}
.service-lists{display:flex;margin-top:24px;font-size:9.6px;color:var(--olive-dark)}
.service-lists ul{list-style:none}
.service-lists li{line-height:1.3;margin-bottom:7.3px;padding-left:9px;position:relative}
.service-lists li::before{content:"•";position:absolute;left:0;color:#999}
.col-a{width:189px}.col-b{width:200px}
.sidebar{position:absolute;left:695px;top:558px;width:241px;height:548px;background:var(--panel)}
.side-title{font-size:21px;font-weight:600;color:var(--olive);padding:28px 18px 10px;border-bottom:1px solid var(--rule)}
.news{list-style:none;padding:17px 18px 0 20px}
.news li{display:flex;gap:11px;margin-bottom:28px}
.date{flex:0 0 41px;height:66px;background:var(--date);color:#fff;text-align:center;font-size:9px;padding-top:8px;position:relative}
.date b{display:block;font-size:17px;font-weight:400;line-height:1.2}
.date span{position:absolute;left:0;bottom:0;width:100%;height:16px;background:var(--olive-box);font-size:8.5px;line-height:16px}
.news p{font-size:8.6px;line-height:1.55;color:#555}
.news a{display:block;font-size:9px;color:#222;margin-top:6px;text-decoration:none}
.newsletter{position:absolute;left:0;top:370px;width:241px;border-top:3px solid #fff}
.newsletter p{font-size:8.6px;line-height:1.6;color:var(--muted);padding:14px 18px 0 19px}
.email{margin:12px 15px 0 19px;height:36px;background:#fff;border:1px solid var(--rule);font-size:8.8px;color:#aaa;padding:11px 13px;position:relative}
.email svg{position:absolute;right:12px;top:12px}
.footer{position:absolute;left:0;top:1106px;width:1021px;height:94px;background:var(--footer);color:var(--footer-text);font-size:9.8px}
.footer-links{position:absolute;left:85px;top:26px;list-style:none;display:flex}
.footer-links li+li::before{content:"|";margin:0 9px;color:#666}
.copyright{position:absolute;left:85px;top:51px}
.social{position:absolute;left:849px;top:34px;display:flex;gap:9px}
.social span{width:22px;height:22px;border-radius:50%;background:#5a5a5a}
</style>
</head>
<body>
<div class="scenery" role="img" aria-label="Misty mountain valley landscape with green hills and pine trees"></div>

<header class="header">
  <div class="brand">
    <div class="brand-mark"></div>
    <div>
      <div class="brand-name">TLM Woxley Osler &amp; Associates</div>
      <div class="brand-tag">Chartered Professional Accountants</div>
    </div>
  </div>
  <div class="search">Search
    <svg width="8" height="8" viewBox="0 0 8 8"><circle cx="3.3" cy="3.3" r="2.5" fill="none" stroke="#888" stroke-width="1.2"/><line x1="5.2" y1="5.2" x2="7.5" y2="7.5" stroke="#888" stroke-width="1.3"/></svg>
  </div>
  <ul class="nav">
    <li class="active">HOME</li><li>PROFILE</li><li>CLIENT SERVICES</li><li>RESOURCES</li><li>CONTACT</li>
  </ul>
</header>

<div class="hero-title">Aenean quam sapien faucibus</div>
<div class="slide-arrow left"><svg width="10" height="14"><polyline points="8,1 2,7 8,13" fill="none" stroke="#ddd" stroke-width="1"/></svg></div>
<div class="slide-arrow right"><svg width="10" height="14"><polyline points="2,1 8,7 2,13" fill="none" stroke="#ddd" stroke-width="1"/></svg></div>

<section class="features">
  <article class="feature">
    <svg width="34" height="36" viewBox="0 0 34 36"><rect x="1" y="1" width="32" height="34" rx="3" fill="none" stroke="#fff" stroke-width="2"/><rect x="5" y="5" width="24" height="7" fill="#fff"/><g fill="#fff"><rect x="5" y="15" width="5" height="4"/><rect x="12" y="15" width="5" height="4"/><rect x="19" y="15" width="5" height="4"/><rect x="26" y="15" width="3" height="4"/><rect x="5" y="22" width="5" height="4"/><rect x="12" y="22" width="5" height="4"/><rect x="19" y="22" width="5" height="4"/><rect x="26" y="22" width="3" height="4"/><rect x="5" y="29" width="5" height="3"/><rect x="12" y="29" width="5" height="3"/><rect x="19" y="29" width="5" height="3"/><rect x="26" y="29" width="3" height="3"/></g></svg>
    <h2>Accounting <small>Services</small></h2>
    <p>Phasellus nisl est, condimentum vitae faucibus in, sollicitudin vel metus. Nunc sit amet consequat risus. Curabitur ac elit leo. In eleifend dui tellus, in scelerisque MORE</p>
  </article>
  <article class="feature">
    <svg width="40" height="36" viewBox="0 0 40 36"><g fill="#fff"><circle cx="10" cy="9" r="5"/><circle cx="30" cy="9" r="5"/><circle cx="20" cy="13" r="6"/><path d="M2 26c0-6 4-9 8-9s6 2 6 2v7z"/><path d="M38 26c0-6-4-9-8-9s-6 2-6 2v7z"/><path d="M9 36c0-9 5-14 11-14s11 5 11 14z"/></g></svg>
    <h2>Consulting <small>Services</small></h2>
    <p>Phasellus nisl est, condimentum vitae faucibus in, sollicitudin vel metus. Nunc sit amet consequat risus. Curabitur ac elit leo. In eleifend dui tellus, in scelerisque MORE</p>
  </article>
  <article class="feature">
    <svg width="36" height="36" viewBox="0 0 36 36"><g fill="none" stroke="#fff" stroke-width="4"><rect x="3" y="3" width="14" height="10" rx="5" transform="rotate(45 10 8)"/><rect x="19" y="23" width="14" height="10" rx="5" transform="rotate(45 26 28)"/><line x1="14" y1="14" x2="22" y2="22"/></g></svg>
    <h2>Resources</h2>
    <p>Phasellus nisl est, condimentum vitae faucibus in, sollicitudin vel metus. Nunc sit amet consequat risus. Curabitur ac elit leo. In eleifend dui tellus, in scelerisque MORE</p>
  </article>
</section>

<main class="main">
  <h1>Welcome the TLM Woxley Osler &amp; Associates</h1>
  <p class="lead">Please note that, as of November 26, 2012, our Quillmarsh office has relocated to 48 Linden Court, Quillmarsh, NB E4B 2K7.&nbsp; Linden Court is located off Marlow Drive, just past Brennan’s Flooring Depot on the Birchfield Road on your way out of the city.</p>
  <p class="copy">In In addition to providing you with a profile of our firm and the services we provide, this Website has been designed to become a helpful resource tool to you, our valued clients and visitors. Our dedication to superior client service has brought us to the Internet as we endeavor to continue to provide the highest quality professional service and guidance.</p>
  <div class="intro-row">
    <div class="desk-photo" role="img" aria-label="Person working on a laptop at a wooden desk with papers and pencils"></div>
    <div>
      <p class="copy">As you browse through our Website, you will see that we have not only highlighted background information on our firm and the services we provide, but have also included useful resources such as informative articles (in our Newsletter section) and interactive financial calculators (in our Financial Tools section). In addition, we have taken the time to gather many links to external Websites that we felt would be of interest to our clients and visitors (in our Internet Links section).</p>
      <p class="copy" style="margin-top:7px">While browsing through our Website, please feel free to contact us with any questions or comments you may have – we’d love to hear from you. We pride ourselves on being proactive and responsive to our clients’ inquiries and suggestions.</p>
    </div>
  </div>
  <div class="service-lists">
    <ul class="col-a">
      <li>Accounting Services</li><li>Financial Statements</li><li>Bookkeeping/Write-Up</li><li>Audit Services</li><li>Reviews &amp; Compilations</li><li>Tax Services</li><li>Payroll Services</li><li>Federal and Provincial Sales Tax</li>
    </ul>
    <ul class="col-b">
      <li>Tax Preparation</li><li>Estate &amp; Trust Tax Preparation</li><li>Tax Planning</li><li>Consulting Services</li><li>Computer Consulting</li><li>Business Succession Planning</li><li>Accounting Software Selection &amp; Implementation</li>
    </ul>
    <ul>
      <li>Business Consulting</li><li>Business Valuations</li><li>Estate Planning</li><li>Financial Planning</li><li>Purchase and Sale of a Business</li><li>Retirement Planning</li><li>Charity Returns</li>
    </ul>
  </div>
</main>

<aside class="sidebar">
  <h2 class="side-title">Latest News</h2>
  <ul class="news">
    <li><div class="date">Apr<b>12</b><span>2015</span></div><div><p>Condimentum vitae faucibus in, sollicitudin vel metus. Nunc sit amet consequat risus. Curabitur ac elit leo. In eleifend dui tellus</p><a href="#">MORE</a></div></li>
    <li><div class="date">Apr<b>12</b><span>2015</span></div><div><p>Condimentum vitae faucibus in, sollicitudin vel metus. Nunc sit amet consequat risus. Curabitur ac elit leo. In eleifend dui tellus</p><a href="#">MORE</a></div></li>
    <li><div class="date">Apr<b>12</b><span>2015</span></div><div><p>Condimentum vitae faucibus in, sollicitudin vel metus. Nunc sit amet consequat risus. Curabitur ac elit leo. In eleifend dui tellus</p><a href="#">MORE</a></div></li>
  </ul>
  <section class="newsletter">
    <h2 class="side-title" style="padding-top:18px">Newsletter Subscribe</h2>
    <p>Condimentum vitae faucibus in, sollicitudin vel metus. Nunc sit amet consequat risus.</p>
    <div class="email">E-mail ID
      <svg width="15" height="11" viewBox="0 0 15 11"><rect width="15" height="11" rx="1" fill="#999"/><polyline points="1,1 7.5,6.5 14,1" fill="none" stroke="#fff" stroke-width="1.2"/></svg>
    </div>
  </section>
</aside>

<footer class="footer">
  <ul class="footer-links"><li>Home</li><li>Profile</li><li>Client Services</li><li>Resources</li><li>Contact</li></ul>
  <p class="copyright">Copyright &nbsp;© &nbsp;2015 &nbsp; TLM Woxley Osler &amp; Associates. &nbsp; All rights reserved.</p>
  <div class="social" aria-label="Social links"><span></span><span></span><span></span></div>
</footer>
</body>
</html>
```